Website for Apartment Rental in Prague

I would like to create designs of my website focused on luxury apartment rentals in Prague, Czech Republic. I created initial mock-ups, They are all attached. I need to design homepage and subpage. The mock-ups were created by combining elements from different websites that I liked but I need you to create a design that is unique and original. The attached files a only a guidance for the structure of the website but not for the design. Try to be creative.

Apartment

```html
<!DOCTYPE html>
<html lang="en">
<head>
<meta charset="utf-8">
<title>Sola Vita Apartment Prague</title>
<link href="https://fonts.googleapis.com/css2?family=Jost:ital,wght@0,400;0,500;0,600;1,400&family=Playfair+Display:wght@600&display=swap" rel="stylesheet">
<style>
:root{
  --accent:#f7b300;
  --ink:#111;
  --text:#333;
  --muted:#666;
  --line:#dcdcdc;
  --band:#efefef;
  --bar:rgba(38,38,38,.78);
  --footer:#101010;
  --white:#fff;
}
*{box-sizing:border-box;margin:0;padding:0}
html,body{width:1200px;height:2293px;overflow:hidden}
body{font-family:"Jost",Arial,sans-serif;color:var(--text);background:var(--white);position:relative}
.wrap{width:916px;margin:0 auto;position:relative}

/* hero */
.hero{position:relative;height:628px;overflow:hidden}
.hero-photo{position:absolute;inset:0;background:linear-gradient(100deg,#5b5b58 0%,#b9b7b0 22%,#dcdad3 45%,#e9e7e1 62%,#cfc6b4 78%,#8f8471 100%)}
.hero-title{position:absolute;top:336px;left:0;right:0;text-align:center;font-family:"Playfair Display",Georgia,serif;font-size:38px;font-weight:600;color:var(--white);letter-spacing:1px;text-shadow:0 2px 6px rgba(0,0,0,.65)}
.dots{position:absolute;top:603px;left:50%;transform:translateX(-50%);display:flex;gap:4px}
.dots span{width:8px;height:8px;border-radius:50%;border:1px solid var(--white)}
.dots span.on{background:var(--white)}

.topbar{position:absolute;top:0;left:0;right:0;height:80px;background:var(--bar);border-bottom:1px solid rgba(255,255,255,.25)}
.topbar .wrap{height:80px;display:flex;align-items:center;font-size:13px;color:var(--white)}
.lang{border:1px solid var(--white);padding:1px 5px;font-size:12px;margin-right:34px}
.top-link{display:flex;align-items:center;gap:8px;margin-right:28px}
.brand{position:absolute;left:50%;transform:translateX(-50%);text-align:center;font-size:17px;font-weight:500;line-height:1.15;color:var(--white)}
.contacts{margin-left:auto;display:flex;align-items:center;gap:22px}
.contacts span{display:flex;align-items:center;gap:8px}
.phone{font-size:15px;font-weight:500}
.mainnav{position:absolute;top:80px;left:0;right:0;height:33px;background:var(--bar)}
.mainnav ul{list-style:none;display:flex;justify-content:space-between;align-items:center;height:33px;width:916px;margin:0 auto;padding:0 3px;font-size:13px;font-weight:500;color:var(--white)}

/* booking */
.booking{height:236px;padding-top:57px}
.booking h2{text-align:center;font-size:25px;font-weight:500;color:var(--ink)}
.accent{color:var(--accent)}
.form{position:relative;height:80px;margin-top:26px}
.field{position:absolute;top:0}
.field label{display:block;font-size:11.5px;color:#222;height:20px}
.box{height:34px;border:1px solid #cfcfcf;border-radius:3px;display:flex;align-items:center;justify-content:space-between;padding:0 9px;font-size:11px;color:#444;background:var(--white)}
.btn-check{position:absolute;top:20px;left:656px;width:129px;height:34px;background:var(--accent);color:var(--white);border-radius:3px;font-size:11.5px;font-weight:500;display:flex;align-items:center;justify-content:center}

/* vision */
.vision{height:502px;background:var(--band);padding-top:54px;text-align:center}
.vision h2{font-size:25px;font-weight:500;color:var(--ink)}
.vision .lead{width:830px;margin:16px auto 0;font-size:13px;line-height:1.5;color:#333}
.badge-icon{width:52px;height:52px;border:2px solid var(--accent);border-radius:50%;margin:22px auto 0;display:flex;align-items:center;justify-content:center}
.designer{margin-top:10px;font-size:14px;font-weight:500;color:var(--ink);line-height:1.25}
.quote{position:relative;width:788px;height:146px;margin:26px auto 0}
.quote-card{position:absolute;inset:0;background:var(--white);transform:skewX(-2deg);border-radius:6px;box-shadow:0 3px 10px rgba(0,0,0,.12)}
.quote-card::before{content:"";position:absolute;top:-14px;left:380px;border:14px solid transparent;border-top:0;border-bottom-color:var(--white)}
.quote p{position:relative;padding:22px 80px 0;font-size:12.5px;font-style:italic;line-height:1.72;color:#333}

/* apartments */
.apartments{position:relative;height:882px}
.card{position:absolute;width:288px;height:362px;border:1px solid var(--line);border-radius:3px;background:var(--white);box-shadow:0 1px 4px rgba(0,0,0,.08)}
.photo{margin:4px 4px 0;height:171px}
.ribbon{position:absolute;top:18px;left:-6px;background:var(--accent);color:var(--white);font-size:11px;font-weight:500;padding:3px 9px;clip-path:polygon(0 0,100% 0,94% 50%,100% 100%,0 100%)}
.card h3{font-size:13px;font-weight:600;color:var(--ink);line-height:1.25;margin:19px 15px 0}
.card .desc{font-size:12.5px;line-height:1.3;color:#333;margin:4px 15px 0;height:56px;overflow:hidden}
.facts{position:absolute;top:283px;left:15px;display:flex;gap:18px;font-size:12.5px;color:#222}
.facts span{display:flex;align-items:center;gap:6px}
.card-foot{position:absolute;left:0;right:0;bottom:0;height:40px;border-top:1px solid var(--line);margin:0 4px;display:flex;justify-content:space-between;align-items:center;padding:0 10px 0 12px;font-size:12.5px;font-weight:500;color:var(--ink)}
.btn-book{border:2px solid var(--accent);padding:2px 12px;font-size:12.5px;font-weight:500}

.info{position:absolute;left:771px;top:455px;width:288px;height:362px;border:1px solid var(--line);background:var(--white);box-shadow:0 1px 4px rgba(0,0,0,.08);text-align:center}
.info h3{height:55px;background:var(--accent);color:var(--white);font-size:22px;font-weight:500;display:flex;align-items:center;justify-content:center}
.info-item{margin:0 14px;padding:18px 0 14px;border-bottom:1px solid var(--line)}
.info-item:last-child{border-bottom:0}
.info-item h4{font-size:15px;font-weight:600;color:var(--ink)}
.info-item p{font-size:12.5px;line-height:1.35;margin-top:6px;color:#333}

/* footer */
.footer{position:absolute;left:0;right:0;top:2248px;height:45px;background:var(--footer)}
.footer .wrap{height:45px;display:flex;align-items:center;font-size:11px;color:#ddd}
.social{position:absolute;left:555px;display:flex;gap:5px}
.social span{width:24px;height:24px;border-radius:50%}
.message{position:absolute;left:836px;top:2240px;width:222px;height:46px;background:var(--accent);color:var(--white);font-size:15px;font-weight:500;display:flex;align-items:center;justify-content:center;gap:8px}
</style>
</head>
<body>

<header class="hero">
  <div class="hero-photo" role="img" aria-label="Bright living room of a Prague apartment with fireplace, sofa, framed pictures and a rocking chair"></div>
  <div class="topbar">
    <div class="wrap">
      <span class="lang">EN ▾</span>
      <span class="top-link">Our Hospitality</span>
      <span class="top-link">
        <svg width="16" height="14" viewBox="0 0 16 14"><path d="M2 1v13" stroke="#fff" stroke-width="1.6"/><path d="M3 1h11l-2.5 3.5L14 8H3z" fill="#fff"/></svg>
        Discover Prague
      </span>
      <div class="brand">Sola Vita<br>Apartment Prague</div>
      <div class="contacts">
        <span>
          <svg width="16" height="14" viewBox="0 0 16 14"><path d="M1 5l7-4 7 4v8H1z M1 5l7 5 7-5" fill="none" stroke="#fff" stroke-width="1.4"/></svg>
          reservation@solavitastay.com
        </span>
        <span class="phone">
          <svg width="14" height="14" viewBox="0 0 24 24"><path d="M6.6 10.8a15.1 15.1 0 0 0 6.6 6.6l2.2-2.2c.3-.3.7-.4 1-.2 1.1.4 2.3.6 3.6.6.6 0 1 .4 1 1V20c0 .6-.4 1-1 1A17 17 0 0 1 3 4c0-.6.4-1 1-1h3.5c.6 0 1 .4 1 1 0 1.3.2 2.5.6 3.6.1.3 0 .7-.2 1z" fill="#fff"/></svg>
          420 555 018 246
        </span>
      </div>
    </div>
  </div>
  <nav class="mainnav">
    <ul>
      <li>Apartments</li><li>Location</li><li>Services</li><li>Gallery</li><li>News</li><li>Exclusive Offers &amp; Tours</li><li>For Families</li><li>Contact Us</li>
    </ul>
  </nav>
  <h1 class="hero-title">Being Home In Prague</h1>
  <div class="dots"><span class="on"></span><span></span><span></span><span></span></div>
</header>

<section class="booking">
  <h2>Official Site - <span class="accent">Best Price Guaranteed</span></h2>
  <div class="wrap form">
    <div class="field" style="left:0;width:148px"><label>Check In Date</label>
      <div class="box">11/19/2017<svg width="13" height="13" viewBox="0 0 13 13"><rect x="1" y="2" width="11" height="10" fill="none" stroke="#444"/><path d="M1 5h11M4 0v3M9 0v3" stroke="#444"/></svg></div></div>
    <div class="field" style="left:159px;width:150px"><label>Check Out Date</label>
      <div class="box">11/21/2017<svg width="13" height="13" viewBox="0 0 13 13"><rect x="1" y="2" width="11" height="10" fill="none" stroke="#444"/><path d="M1 5h11M4 0v3M9 0v3" stroke="#444"/></svg></div></div>
    <div class="field" style="left:320px;width:58px"><label>Adults</label>
      <div class="box">02<svg width="11" height="7" viewBox="0 0 11 7"><path d="M1 1l4.5 4.5L10 1" fill="none" stroke="#444"/></svg></div></div>
    <div class="field" style="left:389px;width:57px"><label>Childrens</label>
      <div class="box">01<svg width="11" height="7" viewBox="0 0 11 7"><path d="M1 1l4.5 4.5L10 1" fill="none" stroke="#444"/></svg></div></div>
    <div class="field" style="left:456px;width:58px"><label>Infants</label>
      <div class="box">00<svg width="11" height="7" viewBox="0 0 11 7"><path d="M1 1l4.5 4.5L10 1" fill="none" stroke="#444"/></svg></div></div>
    <div class="field" style="left:525px;width:121px"><label>Promotional Code</label>
      <div class="box"></div></div>
    <div class="btn-check">Check Availability</div>
    <div class="field" style="left:795px;width:121px"><label>OR</label>
      <div class="box" style="font-size:10px">Select Rental Unit<svg width="11" height="7" viewBox="0 0 11 7"><path d="M1 1l4.5 4.5L10 1" fill="none" stroke="#444"/></svg></div></div>
  </div>
</section>

<section class="vision">
  <h2>A Different <span class="accent">Vision Of Travelling</span></h2>
  <p class="lead">Something spectacular has arrived in the heart of Europe. Steps from Old Town, this rental experience is curated with world-class amenities, exemplary style and a level of convenience you have to experience to believe. Experience the different vision of luxury in center of Prague.</p>
  <div class="badge-icon">
    <svg width="24" height="24" viewBox="0 0 24 24"><path d="M5 3h14v6H5zM4 11h16v3H4zM6 14l-2 8M18 14l2 8M8 17h8" fill="none" stroke="#f7b300" stroke-width="1.8"/></svg>
  </div>
  <p class="designer">Interiors Designed<br>By: <span class="accent">Sola Vita</span></p>
  <div class="quote">
    <div class="quote-card"></div>
    <p>Sola Vita apartments offers short term and as well as long term options in our studio apartments and our one bedroom apartment homes. Our luxurious apartments and high quality customer service have allowed us to dominate the Prague apartment market with a proven track record. Our years of experience and knowledge have made us a premier apartment rental company as we continue to stress the importance of servicing individuals and corporations who are seeking the finest accommodations.</p>
  </div>
</section>

<section class="apartments wrap">
  <article class="card" style="left:0;top:66px">
    <div class="photo" role="img" aria-label="Open kitchen and dining area with white table and yellow flowers" style="background:linear-gradient(135deg,#8a6a55,#d9d3cb 50%,#6b6a68)"></div>
    <span class="ribbon">From 150 USD</span>
    <h3>Brand New Luxury Living Shinning Contemporary Design</h3>
    <p class="desc">The 22nd issue is dedicated to colors...</p>
    <div class="facts"><span><svg width="18" height="12" viewBox="0 0 18 12"><path d="M1 1v10M1 8h16v3M1 6h16M3 3h5v3H3z" fill="none" stroke="#f7b300" stroke-width="1.6"/></svg>1 Bedroom</span><span><svg width="13" height="13" viewBox="0 0 13 13"><circle cx="6.5" cy="3.5" r="3" fill="#f7b300"/><path d="M1 13c0-4 2.5-6 5.5-6s5.5 2 5.5 6z" fill="#f7b300"/></svg>Max 4 People</span></div>
    <div class="card-foot"><span>Details</span><span class="btn-book">Book Now</span></div>
  </article>
  <article class="card" style="left:314px;top:66px">
    <div class="photo" role="img" aria-label="Grey living room with sofa, dining table and pendant lamp" style="background:linear-gradient(135deg,#5d5f63,#cfcfd1 55%,#8b8c8e)"></div>
    <span class="ribbon">From 150 USD</span>
    <h3>Brand New Zen Luxury Living Apartment In The Center Of Prague</h3>
    <p class="desc">Recognized with Grand Voyager Journal 2017 Readers' Choice Award #1 hotel in the world...</p>
    <div class="facts"><span><svg width="18" height="12" viewBox="0 0 18 12"><path d="M1 1v10M1 8h16v3M1 6h16M3 3h5v3H3z" fill="none" stroke="#f7b300" stroke-width="1.6"/></svg>1 Bedroom</span><span><svg width="13" height="13" viewBox="0 0 13 13"><circle cx="6.5" cy="3.5" r="3" fill="#f7b300"/><path d="M1 13c0-4 2.5-6 5.5-6s5.5 2 5.5 6z" fill="#f7b300"/></svg>Max 4 People</span></div>
    <div class="card-foot"><span>Details</span><span class="btn-book">Book Now</span></div>
  </article>
  <article class="card" style="left:629px;top:66px">
    <div class="photo" role="img" aria-label="Wooden kitchen with dining table set for a meal" style="background:linear-gradient(135deg,#8b6a3e,#c8a46b 45%,#6e7e8a)"></div>
    <span class="ribbon">From 150 USD</span>
    <h3>Expedition Prague! Top Loca" Brand New Apartment</h3>
    <p class="desc">for your managementcommittee, showroomsession, incentive trip, product launch, privatization...</p>
    <div class="facts"><span><svg width="18" height="12" viewBox="0 0 18 12"><path d="M1 1v10M1 8h16v3M1 6h16M3 3h5v3H3z" fill="none" stroke="#f7b300" stroke-width="1.6"/></svg>1 Bedroom</span><span><svg width="13" height="13" viewBox="0 0 13 13"><circle cx="6.5" cy="3.5" r="3" fill="#f7b300"/><path d="M1 13c0-4 2.5-6 5.5-6s5.5 2 5.5 6z" fill="#f7b300"/></svg>Max 4 People</span></div>
    <div class="card-foot"><span>Details</span><span class="btn-book">Book Now</span></div>
  </article>
  <article class="card" style="left:0;top:455px">
    <div class="photo" role="img" aria-label="Bright living room with red sofa and wooden floor" style="background:linear-gradient(135deg,#c9b28a,#eee6d8 50%,#b7543f)"></div>
    <span class="ribbon">From 150 USD</span>
    <h3>Brand New Zen Luxury Living Apartment In The Center Of Prague</h3>
    <p class="desc">The 22nd issue is dedicated to colors...</p>
    <div class="facts"><span><svg width="18" height="12" viewBox="0 0 18 12"><path d="M1 1v10M1 8h16v3M1 6h16M3 3h5v3H3z" fill="none" stroke="#f7b300" stroke-width="1.6"/></svg>1 Bedroom</span><span><svg width="13" height="13" viewBox="0 0 13 13"><circle cx="6.5" cy="3.5" r="3" fill="#f7b300"/><path d="M1 13c0-4 2.5-6 5.5-6s5.5 2 5.5 6z" fill="#f7b300"/></svg>Max 4 People</span></div>
    <div class="card-foot"><span>Details</span><span class="btn-book">Book Now</span></div>
  </article>
  <article class="card" style="left:314px;top:455px">
    <div class="photo" role="img" aria-label="White bedroom with large windows and a blue rug" style="background:linear-gradient(135deg,#d8d5cf,#f1efec 50%,#9a8a78)"></div>
    <span class="ribbon">From 150 USD</span>
    <h3>Brand New Modern Apartment Unbeatable Location</h3>
    <p class="desc">Recognized with Grand Voyager Journal 2017</p>
    <div class="facts"><span><svg width="18" height="12" viewBox="0 0 18 12"><path d="M1 1v10M1 8h16v3M1 6h16M3 3h5v3H3z" fill="none" stroke="#f7b300" stroke-width="1.6"/></svg>1 Bedroom</span><span><svg width="13" height="13" viewBox="0 0 13 13"><circle cx="6.5" cy="3.5" r="3" fill="#f7b300"/><path d="M1 13c0-4 2.5-6 5.5-6s5.5 2 5.5 6z" fill="#f7b300"/></svg>Max 4 People</span></div>
    <div class="card-foot"><span>Details</span><span class="btn-book">Book Now</span></div>
  </article>
  <aside class="info">
    <h3>Need To Know</h3>
    <div class="info-item"><h4>APARTMENTS</h4><p>Also Avaliable To Rent All The Apartments<br>Together For Companies Or Larger Groups,</p></div>
    <div class="info-item"><h4>CHECK-OUT</h4><p>12 Noon; Earliest Check-in, 3PM- Both<br>Are Flexible, By Arragement.</p></div>
    <div class="info-item"><h4>RATES</h4><p>Prices From 150 USD Per Night<br>Including Tax</p></div>
  </aside>
</section>

<footer class="footer">
  <div class="wrap">
    <span>Copyright © 2017 Sola Vita Apartment Prague. All Rights Reserved.</span>
    <div class="social">
      <span style="background:#3b5a98"></span><span style="background:#3aa6e0"></span><span style="background:#0f77b3"></span><span style="background:#d34836"></span>
    </div>
  </div>
</footer>
<div class="message">
  <svg width="18" height="16" viewBox="0 0 18 16"><path d="M9 1C4.6 1 1 3.8 1 7.2c0 1.8 1 3.4 2.6 4.5L3 15l3.6-2.2c.8.2 1.6.3 2.4.3 4.4 0 8-2.8 8-6.2S13.4 1 9 1z" fill="#fff"/><circle cx="5.5" cy="7.2" r="1" fill="#f7b300"/><circle cx="9" cy="7.2" r="1" fill="#f7b300"/><circle cx="12.5" cy="7.2" r="1" fill="#f7b300"/></svg>
  Please Leave a Message
</div>

</body>
</html>
```